Luxury Japanese Matcha Green Tea Packaging Full Packet Design

We're looking for a quality full pack design (front and back) for Ceremonial Grade and Premium Grade Matcha to sell on Bazaarly. We need a 2D versions of front and back images in photoshop and JPG. We also need a 3D versions of front and back for marketing purposes.

You can see our current styling and pack at www.brewvantis.co.uk. However, we want to improve the design and go more professional, simple and elegant with the brand. The last design was from 3 years a go. But hopefully you can see what we are about.

The design will be identical both both packs:

Pack 1: 230mm x 140mm - Premium Grade
Pack 2: 170mm x 120mm - Ceremonial Grade

The design needs to fit both sizes, with pack 1 saying Premium Grade and pack 2 saying Ceremonial Grade.

As many colours as needed, printing is CMYK + White digital printed.

Front of pack:

Product Headline:

Organic Handpicked
Stoneground Japanese Matcha
Green Tea Powder

抹茶

Text: Premium Grade (pack 1) / Ceremonial Grade (pack 2)

100g (pack 1) / 40g (pack 2)

(EU Organic logo)

Back of pack:

Organic Certified GB-ORG-19
Stone Ground Ceremonial Grade Matcha from Uji

Ingredients: 100% Organic Matcha Green Tea Powder

Place of origin: Japan, Store in a cool, dry, dark place
Keep sealed at all times, Best Before 31/03/2020
Not recommended for use if pregnant or nursing

Your next order is ready for you at www.KelpHour.co.uk

Preparing Traditional Matcha Tea:
Sift 1-2g or 1/2 teaspoon of Matcha Green Tea
powder into a bowl or large cup. Add 1/2 cup of hot water
at drinking temperature. Whisk with Bamboo or
Electric Whisk until frothy. Drink immediately.

Preparing Matcha Latte:
Sift 1-2g of Matcha Power into a cup, mix in 2-3 tablespoons of hot water.
Add hot milk and sweetener if desired. Whisk thoroughly.

Nutritional Information:

Per 1g Per 100g
Energy 14.44kJ 1446kJ
3.44kCal 345kCal
Fat 0.04g 4g
Saturates <0.01g 0.6g
Carbohydrates 0.76g 76g
of which sugars 0.47g 47.2g
Protein 0.144g 14.5g
Salt <0.01g 126mg

Per 1g Per 100g
Calcium 1.88mg 191mg
Potassium 94.8mg 3750mg
Iron <0.1g 1.6mg
Zinc <0.1g 1.72mg
Vitamin A 120µg (15% RDA) 2400µg (150% RDA)
Vitamin C 3mg (4% RDA) 60mg (75% RDA)
Folic acid 6µg (6% RDA) 60µg (30% RDA)
Riboflavin 0.1mg (4% RDA) 1.4mg (96% RDA)
Caffeine 17mg 1700mg

Quillon Harbour Ltd. T/A Brewvantis
Company Number: 05617429
Registered Office: 7 The Yard, Darnwick Cl
Newbury, Berkshire, RG17 2QH
social@brewvantis.co.uk
Local Call +44 (0) 20 3184 6057 / Freephone +44 (0) 800 512 7736

This supplement should not be used as a substitute for a varied diet Do not exceed the recommended daily dose.

For more information on Matcha, download the free eBook at www.TheLeafPrimer.com

Please consult a healthcare practitioner if you are pregnant or taking prescription medicine before using this product.

Recommended daily dose

1-5g daily

Storage information: Store in a cool dry place away from sunlight, moisture, and heat. Keep contents dry.

Logos for back of pack:
EU Organic logo with 'GB-ORG-19 Non-EU Agriculture' written directly underneath it.
Vegan logo
Natural Crop Alliance logo
Bazaarly Barcode

Additional deisgn notes:

We have included a design that we like.

The top 2cm will be torn off by the user, so should not contain any key information.

Target Market(s)

High End health and wellness Consumers

Colors
acd036
0455a3
edf8f6

Requirements
Must have
• Stand out on Bazaarly. Show the product to be premium.

```html
<!DOCTYPE html>
<html lang="en">
<head>
<meta charset="utf-8">
<title>Ceremonial Grade Matcha – Back of Pack</title>
<link href="https://fonts.googleapis.com/css2?family=Quicksand:wght@400;500;700&display=swap" rel="stylesheet">
<style>
  :root {
    --brand-blue: #0455a3;
    --brand-green: #acd036;
    --mint: #edf8f6;
    --cell: #eef6f5;
    --ink-grey: #3c3c3c;
    --white: #ffffff;
  }
  * { margin: 0; padding: 0; box-sizing: border-box; }
  html, body { width: 730px; height: 1200px; overflow: hidden; background: var(--white); }
  body { font-family: "Quicksand", sans-serif; color: var(--brand-blue); }
  .pack-back { position: relative; width: 730px; height: 1200px; background: var(--white); overflow: hidden; }
  .backdrop { position: absolute; inset: 0; }
  .block { position: absolute; font-size: 12.5px; line-height: 15.6px; }
  .block strong { font-weight: 700; }
  .cert-line { position: absolute; left: 78px; top: 259px; font-size: 13px; }
  .product-title { position: absolute; left: 78px; top: 278px; font-size: 21px; font-weight: 400; letter-spacing: 0.2px; }
  .product-title strong { font-weight: 700; }
  .ingredients { left: 78px; top: 342px; }
  .origin { left: 78px; top: 388px; }
  .reorder-band { position: absolute; left: 0; top: 513px; width: 354px; height: 36px; background: var(--brand-blue); color: var(--white); font-size: 12.5px; line-height: 15px; padding: 3px 0 0 78px; }
  .prep-tea { left: 78px; top: 584px; width: 290px; }
  .prep-latte { left: 78px; top: 692px; width: 290px; }
  .company { left: 78px; top: 786px; width: 290px; }
  .nutrition-heading { position: absolute; left: 382px; top: 342px; font-size: 12.5px; font-weight: 700; }
  .nutrition { position: absolute; left: 382px; top: 360px; border-collapse: separate; border-spacing: 2px; font-size: 8.6px; }
  .nutrition th { background: var(--brand-blue); color: var(--white); font-weight: 500; height: 15px; }
  .nutrition th.blank { background: transparent; }
  .nutrition td { background: var(--cell); height: 15px; color: var(--brand-blue); }
  .nutrition td:first-child { width: 78px; padding-left: 2px; }
  .nutrition td:nth-child(2), .nutrition th:nth-child(2) { width: 83px; text-align: center; }
  .nutrition td:nth-child(3), .nutrition th:nth-child(3) { width: 97px; text-align: center; }
  .cert-badges { position: absolute; left: 382px; top: 832px; }
  .badge { position: absolute; }
  .badge-vegan { left: 0; top: 2px; width: 58px; height: 58px; border-radius: 50%; background: var(--white); border: 3px solid var(--brand-green); }
  .badge-crop { left: 74px; top: 4px; width: 38px; height: 58px; background: #2f8a3a; border-radius: 4px; }
  .badge-eu { left: 130px; top: 2px; width: 83px; height: 54px; background: #8bbf3f; }
  .eu-caption { position: absolute; left: 130px; top: 62px; font-size: 8.6px; line-height: 11px; color: #222; }
  .footer-notes { left: 78px; top: 983px; width: 380px; }
  .footer-notes p { margin-bottom: 15px; }
  .dose { left: 478px; top: 1030px; width: 200px; }
  .dose p { margin-bottom: 15px; }
</style>
</head>
<body>
<main class="pack-back">
  <svg class="backdrop" width="730" height="1200" viewBox="0 0 730 1200" aria-hidden="true">
    <defs>
      <linearGradient id="leafWash" x1="0" y1="0" x2="1" y2="1">
        <stop offset="0" stop-color="#e3efe9"/>
        <stop offset="0.6" stop-color="#dbe8d8"/>
        <stop offset="1" stop-color="#e8f2ea"/>
      </linearGradient>
    </defs>
    <polygon points="0,0 730,0 730,300 0,200" fill="var(--mint)"/>
    <polygon points="0,896 730,992 730,1200 0,1200" fill="var(--mint)"/>
  </svg>
  <svg style="position:absolute;left:0;top:0" width="730" height="300" viewBox="0 0 730 300" role="img" aria-label="Hand-drawn line illustration of tea leaves, a lime slice, a matcha whisk and a bowl of green matcha">
    <polygon points="0,0 730,0 730,240 0,200" fill="url(#leafWash)"/>
  </svg>

  <p class="cert-line">Organic Certified GB-ORG-19</p>
  <h1 class="product-title">Stone Ground Ceremonial Grade <strong>Matcha</strong> from Uji</h1>

  <div class="block ingredients"><strong>Ingredients:</strong><br>100% Organic Matcha Green Tea Powder</div>
  <div class="block origin"><strong>Place of origin:</strong> Japan,<br>Store in a cool, dry, dark place<br>Keep sealed at all times<br>Best Before 31/03/2020<br>Not recommended for use<br>if pregnant or nursing</div>

  <div class="reorder-band">Your next order is ready for<br>you at www.KelpHour.co.uk</div>

  <div class="block prep-tea"><strong>Preparing Traditional Matcha Tea:</strong><br>Sift 1-2g or 1/2 teaspoon of Matcha Green Tea powder into a bowl or large cup. Add 1/2 cup of hot water at drinking temperature. Whisk with Bamboo or Electric Whisk until frothy. Drink immediately.</div>
  <div class="block prep-latte"><strong>Preparing Matcha Latte:</strong><br>Sift 1-2g of Matcha Power into a cup, mix in 2-3 tablespoons of hot water. Add hot milk and sweetener if desired. Whisk thoroughly.</div>

  <div class="block company">Quillon Harbour Ltd. T/A Brewvantis<br>Company Number: 05617429<br>Registered Office: 7 The Yard, Darnwick Cl<br>Newbury, Berkshire, RG17 2QH<br>social@brewvantis.co.uk<br>Local Call +44 (0) 20 3184 6057 / Freephone +44 (0) 800 512 7736</div>

  <h2 class="nutrition-heading">Nutritional Information:</h2>
  <table class="nutrition">
    <thead><tr><th class="blank"></th><th>Per 1g</th><th>Per 100g</th></tr></thead>
    <tbody>
      <tr><td>Energy</td><td>14.44kJ</td><td>1446kJ</td></tr>
      <tr><td></td><td>3.44kCal</td><td>345kCal</td></tr>
      <tr><td>Fat</td><td>0.04g</td><td>4g</td></tr>
      <tr><td>Saturates</td><td>&lt;0.01g</td><td>0.6g</td></tr>
      <tr><td>Carbohydrates</td><td>0.76g</td><td>76g</td></tr>
      <tr><td>of which sugars</td><td>0.47g</td><td>47.2g</td></tr>
      <tr><td>Protein</td><td>0.144g</td><td>14.5g</td></tr>
      <tr><td>Salt</td><td>&lt;0.01g</td><td>126mg</td></tr>
      <tr><td>Calcium</td><td>1.88mg</td><td>191mg</td></tr>
      <tr><td>Potassium</td><td>94.8mg</td><td>3750mg</td></tr>
      <tr><td>Iron</td><td>&lt;0.1g</td><td>1.6mg</td></tr>
      <tr><td>Zinc</td><td>&lt;0.1g</td><td>1.72mg</td></tr>
      <tr><td>Vitamin A</td><td>120µg (15% RDA)</td><td>2400µg (150% RDA)</td></tr>
      <tr><td>Vitamin C</td><td>3mg (4% RDA)</td><td>60mg (75% RDA)</td></tr>
      <tr><td>Folic acid</td><td>6µg (6% RDA)</td><td>60µg (30% RDA)</td></tr>
      <tr><td>Riboflavin</td><td>0.1mg (4% RDA)</td><td>1.4mg (96% RDA)</td></tr>
      <tr><td>Caffeine</td><td>17mg</td><td>1700mg</td></tr>
    </tbody>
  </table>

  <div class="cert-badges">
    <div class="badge badge-vegan" role="img" aria-label="Vegan certification badge"></div>
    <div class="badge badge-crop" role="img" aria-label="Natural Crop Alliance certified organic badge"></div>
    <div class="badge badge-eu" role="img" aria-label="EU organic certification badge"></div>
    <p class="eu-caption">GB-ORG-19<br>Non-EU Agriculture</p>
  </div>

  <div class="block footer-notes">
    <p>This supplement should not be<br>used as a substitute for a varied diet</p>
    <p>Do not exceed the recommended daily dose.</p>
    <p>For more information on Matcha, download the<br>free eBook at www.TheLeafPrimer.com</p>
    <p>Please consult a healthcare practitioner if you are pregnant<br>or taking prescription medicine before using this product.</p>
  </div>

  <div class="block dose">
    <p>Recommended daily dose<br><strong>1-5g daily</strong></p>
    <p><strong>Storage information:</strong><br>Store in a cool dry place<br>away from sunlight, moisture,<br>and heat. Keep contents dry.</p>
  </div>
</main>
</body>
</html>
```